Design a New Business Card for Our Company

We are looking for fresh, unique, and a modern business card that reflects our roots as digital marketing agency focused on SEM.

Industry/Entity Type

Marketing

Contact Information for Business Card

looking for very unique out of the box designs. clean and modern that compliments our logo

Requirements
Must have
• colors should match our logo
• Front should have name, address, email, and phone/fax of the person, phone/fax are the same number
• back should have our url

```html
<!DOCTYPE html>
<html lang="en">
<head>
<meta charset="utf-8">
<title>Clearpath Solutions – Business Card</title>
<link rel="stylesheet" href="https://fonts.googleapis.com/css2?family=Open+Sans:wght@400;600&display=swap">
<style>
  :root {
    --backdrop: #3c3c3c;
    --card: #ffffff;
    --brand-blue: #5b97d1;
    --grey-text: #a3a3a3;
    --ink: #3a3a3a;
    --icon-grey: #b0b0b0;
    --decor-grey: #ececec;
  }
  * { margin: 0; padding: 0; box-sizing: border-box; }
  html, body {
    width: 1105px; height: 1200px; overflow: hidden;
    background: var(--backdrop);
    font-family: "Open Sans", Arial, sans-serif;
  }
  .canvas { position: relative; width: 1105px; height: 1200px; }

  .card {
    position: absolute; left: 196px; width: 720px; height: 413px;
    background: var(--card);
  }
  .card--front { top: 145px; }
  .card--back { top: 602px; }

  /* Front */
  .front-decor {
    position: absolute; left: 47px; top: 77px;
    width: 260px; height: 260px; border-radius: 50%;
    background: var(--decor-grey);
  }
  .front-details {
    position: absolute; right: 46px; top: 54px;
    text-align: right;
  }
  .brand-name {
    color: var(--brand-blue); font-weight: 600; line-height: 1;
  }
  .brand-name__main { display: block; font-size: 56px; letter-spacing: -1px; }
  .brand-name__sub { display: block; font-size: 16px; letter-spacing: 11px; margin-right: -11px; margin-top: 4px; }

  .person-name { margin-top: 26px; font-size: 25px; font-weight: 600; color: var(--grey-text); line-height: 1.1; }
  .person-role { font-size: 19px; color: var(--brand-blue); line-height: 1.3; }
  .address { margin-top: 18px; font-size: 19px; color: var(--ink); line-height: 1.38; font-style: normal; }
  .contact-list { list-style: none; margin-top: 18px; }
  .contact-list li {
    display: flex; justify-content: flex-end; align-items: center; gap: 8px;
    font-size: 18px; color: var(--ink); line-height: 1.6;
  }
  .contact-list svg { width: 17px; height: 17px; fill: var(--icon-grey); }

  /* Back */
  .back-brand {
    position: absolute; left: 0; right: 0; top: 160px;
    display: flex; justify-content: center; align-items: center; gap: 18px;
  }
  .back-brand__dot { width: 40px; height: 40px; border-radius: 50%; background: var(--brand-blue); }
  .back-brand .brand-name__main { font-size: 52px; text-align: left; }
  .back-brand .brand-name__sub { font-size: 14px; letter-spacing: 10px; }
  .web-address {
    position: absolute; left: 0; right: 0; top: 347px;
    text-align: center; font-size: 18px; letter-spacing: 4px; color: var(--ink);
  }
</style>
</head>
<body>
<main class="canvas">

  <section class="card card--front" aria-label="Card front">
    <div class="front-decor"></div>
    <div class="front-details">
      <div class="brand-name">
        <span class="brand-name__main">clearpath</span>
        <span class="brand-name__sub">SOLUTIONS</span>
      </div>
      <p class="person-name">Daniel Reyes</p>
      <p class="person-role">CEO/Founder</p>
      <address class="address">2140 Willow Crest Road<br>Juneau, Alaska 34512</address>
      <ul class="contact-list">
        <li>555 214 7730
          <svg viewBox="0 0 24 24" aria-hidden="true"><path d="M6.6 10.8a15.1 15.1 0 0 0 6.6 6.6l2.2-2.2a1 1 0 0 1 1-.25 11.4 11.4 0 0 0 3.6.57 1 1 0 0 1 1 1V20a1 1 0 0 1-1 1A17 17 0 0 1 3 4a1 1 0 0 1 1-1h3.5a1 1 0 0 1 1 1c0 1.25.2 2.45.57 3.57a1 1 0 0 1-.25 1z"/></svg>
        </li>
        <li>555 214 7731
          <svg viewBox="0 0 24 24" aria-hidden="true"><path d="M6 3h10v5H6zM3 9h18v8h-3v4H6v-4H3zm5 6v4h8v-4z"/></svg>
        </li>
        <li>hello@clearpathsem.com
          <svg viewBox="0 0 24 24" aria-hidden="true"><path d="M2 5h20v14H2zm2 2v.5l8 5 8-5V7z"/></svg>
        </li>
      </ul>
    </div>
  </section>

  <section class="card card--back" aria-label="Card back">
    <div class="back-brand">
      <span class="back-brand__dot"></span>
      <div class="brand-name">
        <span class="brand-name__main">clearpath</span>
        <span class="brand-name__sub">SOLUTIONS</span>
      </div>
    </div>
    <p class="web-address">www.clearpathsem.com</p>
  </section>

</main>
</body>
</html>
```